Personal Training Business at home (Fern Vitality & Health)

My business name will be Fern Vitality & Health and will be training people with special needs (Asthma, Diabetes, Obesity, Rehab, Sports Performance) for all ages. It will be set indoor and outdoor for all types of weather conditions. I,m also doing Pilates group classes as well in a Japanese garden setting.I will be working alone so the groups will be small and the client has a high quality of service. I just need something very basic to start with then as the business expands I can edit it to it,s growth.

Target Market(s)

Target special population persons with dysfunctions injuries, metabolic/cardio-respiratory conditions, sports performance and more also healthy food choices.

Industry/Entity Type

Business

Number of Pages Required

3 page

Font styles to use
Serif

Colors
f78f20
ffffff
474747
cbcbcb
abd036

Requirements
Must have
• The website must have accessibility for change, to be able to link on other networks like my own YouTube videos. A basic lay out so I can fill in the pages and ad more as I expand the business. The logo to have the A for Fern to be an image of a man shaped as the letter A with his arms extended out/up. Private Facility and must ring for appointment to enter premises.
Nice to have
• The Image I want to have in my studio is for people to be serious about training & health choices. I want them to be able to train in a comfortable environment and free of air conditioned concrete rooms with machines. My home is converted to a Organic feature and outdoor/indoor training facility that my clients & I can share the natural freedom of training in the elements. My client have special needs and need extra care, they are people with injuries, metabolic/cardio-respiratory condition, asthmatics & more they need to be screened and tested for the condition that they suffer from and together with there allied professional we work together to treat them with the up most care for maximum results. This is what I want to target I long term client with real Goals on there mind and not some pipe dream.
Should not have
• Not to be portray as a Gym with machines and clients that only care about image.

```html
<!DOCTYPE html>
<html lang="en">
<head>
<meta charset="utf-8">
<title>Fern Vitality &amp; Health</title>
<link rel="stylesheet" href="https://fonts.googleapis.com/css2?family=Open+Sans:wght@400;600;700;800&family=Roboto:wght@400;500;700&display=swap">
<style>
:root{
  --green:#abd036;
  --orange:#f78f20;
  --white:#ffffff;
  --ink:#474747;
  --grey:#cbcbcb;
  --icon:#8a8a8a;
  --soc-a:#2b4a8b;
  --soc-b:#1da1e0;
  --soc-c:#ee5a24;
}
*{margin:0;padding:0;box-sizing:border-box}
html,body{width:1200px;height:1156px;overflow:hidden;background:var(--white)}
body{position:relative;font-family:'Roboto',sans-serif;color:var(--ink)}
.abs{position:absolute}

.site-header{left:0;top:0;width:1200px;height:106px;background:var(--green)}
.brand{left:160px;top:24px;display:flex;align-items:center;gap:10px;color:var(--white);font-family:'Open Sans',sans-serif;font-weight:800;font-size:31px;letter-spacing:.2px}
.brand-dot{width:22px;height:22px;border-radius:50%;background:var(--white)}
.contact-item{color:var(--white);font-family:'Open Sans',sans-serif}
.contact-label{font-size:11px;font-weight:700;letter-spacing:2px;display:block}
.contact-value{font-weight:700;display:flex;align-items:center;gap:8px}
.contact-email{left:668px;top:40px}
.contact-email .contact-label{margin-left:20px}
.contact-email .contact-value{font-size:14px;margin-top:1px}
.contact-phone{left:914px;top:36px}
.contact-phone .contact-label{margin-left:23px}
.contact-phone .contact-value{font-size:18px}
.header-divider{left:886px;top:40px;width:1px;height:32px;background:rgba(255,255,255,.55)}

.main-nav{left:0;top:106px;width:1200px;height:33px;background:var(--orange)}
.main-nav ul{list-style:none;display:flex;height:33px;padding-left:152px;font-family:'Open Sans',sans-serif;font-size:12px;font-weight:700;color:var(--white)}
.main-nav li{display:flex;align-items:center;padding:0 13px;position:relative;height:33px}
.main-nav li.sep::before{content:"";position:absolute;left:0;top:9px;height:16px;width:1px;background:rgba(255,255,255,.8)}
.main-nav li.active{background:var(--green);padding:0 15px}
.nav-gap{width:6px}

.hero{left:0;top:139px;width:1200px;height:328px;background:linear-gradient(180deg,#3d4a34 0%,#5b5d45 35%,#8a6347 62%,#6b4a36 100%)}
.hero-title{left:0;top:220px;width:1200px;text-align:center;color:var(--white);font-family:'Open Sans',sans-serif;font-size:31px;font-weight:400}
.hero-title strong{font-weight:700}
.hero-dots{left:541px;top:286px;display:flex;gap:19px;align-items:center}
.hero-dots span{width:9px;height:9px;border-radius:50%;background:var(--white)}
.hero-dots span.current{width:13px;height:13px;background:transparent;border:2px solid var(--white)}

.about-title{left:162px;top:505px;font-size:23px;font-weight:400;color:var(--orange)}
.about-text{left:162px;top:551px;width:484px;font-size:12.3px;line-height:24px;text-align:justify}
.about-text em{font-style:normal;font-weight:700;font-size:14px;color:var(--green)}
.portrait{left:754px;top:515px;width:285px;height:315px;background:linear-gradient(160deg,#5f6a55 0%,#7d8a5e 40%,#4c6f8f 100%)}

.site-footer{left:0;top:881px;width:1200px;height:275px;background:var(--green)}
.foot-title{top:32px;font-family:'Open Sans',sans-serif;font-size:11.5px;font-weight:600;color:#3a3a3a}
.field{background:var(--white);display:flex;align-items:flex-start;gap:6px;padding:11px 10px;font-size:11px;color:#555}
.field svg{flex:none;margin-top:1px}
.btn{background:var(--orange);color:var(--white);font-family:'Open Sans',sans-serif;font-weight:700;letter-spacing:2px;display:flex;align-items:center;justify-content:center}
.footer-menu{left:420px;top:58px;list-style:none;font-size:10.8px;line-height:18.8px;color:#3e3e3e}
.social{left:637px;display:flex;align-items:center;gap:12px;font-size:11px;color:#3e3e3e}
.social-dot{width:39px;height:39px;border-radius:50%}
.foot-brand{left:867px;top:205px;display:flex;align-items:center;gap:8px;color:var(--white);font-family:'Open Sans',sans-serif;font-weight:800;font-size:27px}
.foot-brand .brand-dot{width:18px;height:18px}
.copyright{left:866px;top:235px;font-size:9.5px;color:#3e3e3e}
</style>
</head>
<body>

<header class="site-header abs">
  <div class="brand abs"><span class="brand-dot"></span>Fern Fitness</div>
  <div class="contact-item contact-email abs">
    <span class="contact-label">E MAIL US</span>
    <span class="contact-value">
      <svg width="12" height="9" viewBox="0 0 12 9"><rect width="12" height="9" rx="1" fill="#fff"/><path d="M0.5 0.8 6 5 11.5 0.8" stroke="#abd036" stroke-width="1.2" fill="none"/></svg>
      fernfithealth@mailbox.test
    </span>
  </div>
  <div class="header-divider abs"></div>
  <div class="contact-item contact-phone abs">
    <span class="contact-label">CALL US ON</span>
    <span class="contact-value">
      <svg width="9" height="14" viewBox="0 0 9 14"><rect x="0.8" y="0.8" width="7.4" height="12.4" rx="1.5" fill="none" stroke="#fff" stroke-width="1.6"/><rect x="3" y="10.3" width="3" height="1.2" fill="#fff"/></svg>
      0400 555 123
    </span>
  </div>
</header>

<nav class="main-nav abs">
  <ul>
    <li>Home</li>
    <li class="active">About FERN FIT &amp; HEALTH</li>
    <li>Why train with us</li>
    <li class="sep">Training services</li>
    <li class="sep">Location<span class="nav-gap"></span></li>
    <li class="sep">Pricing &amp; packages</li>
    <li class="sep">Facilities</li>
    <li class="sep"><span class="nav-gap"></span>Contact Us</li>
  </ul>
</nav>

<section class="hero abs" role="img" aria-label="Wooden deck in a Japanese garden with bonsai trees on stands">
</section>
<h1 class="hero-title abs"><strong>ORGANIC</strong> Pilates experience</h1>
<div class="hero-dots abs"><span></span><span class="current"></span><span></span><span></span><span></span></div>

<h2 class="about-title abs">About FERN FIT &amp; HEALTH</h2>
<p class="about-text abs">FERNFIT has trainers that have a Diploma of fitness from the Cedar institute&amp; are trained and qualified with the latest training techniques available anywhere in Australia, to give clients a better &amp; more reliable service with cutting edge training programs and testing. The foundation of this business will be to service clients by functional training techniques and some machines, with a combination of group classes &amp; one on one Personal training. We also have an area for Pilates experience this is a very Japanese influenced setting &amp; is called, <em>Organic Pilates experience.</em></p>
<div class="portrait abs" role="img" aria-label="Portrait photo of the trainer in a blue shirt in front of a garden"></div>

<footer class="site-footer abs">
  <h3 class="foot-title abs" style="left:160px">QUICK CONTACT</h3>
  <div class="field abs" style="left:162px;top:62px;width:164px;height:35px">
    <svg width="9" height="10" viewBox="0 0 9 10"><circle cx="4.5" cy="2.6" r="2.4" fill="#8a8a8a"/><path d="M0 10c0-3.2 2-4.8 4.5-4.8S9 6.8 9 10z" fill="#8a8a8a"/></svg>Name
  </div>
  <div class="field abs" style="left:162px;top:102px;width:164px;height:35px">
    <svg width="10" height="8" viewBox="0 0 10 8"><rect width="10" height="8" rx="1" fill="#8a8a8a"/><path d="M0.5 0.8 5 4.2 9.5 0.8" stroke="#fff" stroke-width="1" fill="none"/></svg>E mail
  </div>
  <div class="field abs" style="left:162px;top:142px;width:164px;height:65px">
    <svg width="10" height="10" viewBox="0 0 10 10"><rect x="0.5" y="1.5" width="7.5" height="8" fill="none" stroke="#8a8a8a"/><path d="M4 6 9 1" stroke="#8a8a8a" stroke-width="1.4"/></svg>Message
  </div>
  <div class="btn abs" style="left:243px;top:218px;width:83px;height:26px;font-size:12px">SUBMIT</div>

  <h3 class="foot-title abs" style="left:420px">MENU</h3>
  <ul class="footer-menu abs">
    <li>Home</li>
    <li>About FERN FIT &amp; HEALTH</li>
    <li>Why train with us</li>
    <li>Training services</li>
    <li>Our Location</li>
    <li>Trading hours</li>
    <li>Pricing &amp; packages</li>
    <li>Facilities</li>
    <li>Contact Us</li>
  </ul>

  <h3 class="foot-title abs" style="left:637px">FOLLOW US ON</h3>
  <div class="social abs" style="top:58px"><span class="social-dot" style="background:var(--soc-a)"></span>Community page</div>
  <div class="social abs" style="top:106px"><span class="social-dot" style="background:var(--soc-b)"></span>News stream</div>
  <div class="social abs" style="top:154px"><span class="social-dot" style="background:var(--soc-c)"></span>RSS Feed</div>

  <h3 class="foot-title abs" style="left:848px">NEWSLETTER SIGNUP!</h3>
  <div class="field abs" style="left:849px;top:63px;width:190px;height:37px">
    <svg width="9" height="10" viewBox="0 0 9 10"><circle cx="4.5" cy="2.6" r="2.4" fill="#8a8a8a"/><path d="M0 10c0-3.2 2-4.8 4.5-4.8S9 6.8 9 10z" fill="#8a8a8a"/></svg>Name
  </div>
  <div class="btn abs" style="left:849px;top:109px;width:190px;height:37px;font-size:13px">SIGNUP!</div>
  <div class="foot-brand abs"><span class="brand-dot"></span>Fern Fitness</div>
  <p class="copyright abs">Copyrights @ 2016 All Rights Reserved</p>
</footer>

</body>
</html>
```